Seeking funky, innovative business cards

I am looking to refresh our current business cards to something more engaging, visual and impactful. We are a management consultancy firm, see website (www.larkstone-partners.com.au). I've included our colour scheme, sample of the slides we use and our old business cards. We would like our cards to have icons. The card should display:- Name- Title- Mobile number- Address- Email address- Website - Company logo- Our purpose statement "we build the finest spaces where people thrive"

Contact Information for Business Card

Brennan Ulfsson
Consultant
0468 927 341
Level 3, 218 Wexley Street, Melbourne 3000
brennan@larkstone-partners.com.au
www.larkstone-partners.com.au

Purpose statement "we build the finest spaces where people thrive"
LOGO available in google images

Font styles to use
Other font styles liked:
• Open Sans Light, Bebas Neue (open to other cool foints)

Colors
ffc214
5c5c5c
f5f5f5
fefefe

Requirements
Must have
• - Name
• - Title
• - Mobile number
• - Address
• - Email address
• - Website
• - Company logo
• - Our purpose statement "we build the finest spaces where people thrive"
Nice to have
• - Icons
• - Colour (see our colour scheme"

```html
<!DOCTYPE html>
<html lang="en">
<head>
<meta charset="utf-8">
<title>Larkstone Partners — Business Card</title>
<link rel="stylesheet" href="https://fonts.googleapis.com/css2?family=Roboto:ital,wght@0,300;0,400;0,500;1,400&family=Roboto+Condensed:ital,wght@0,400;0,700;1,400&display=swap">
<style>
  :root {
    --backdrop: #b9b9b9;
    --paper: #ffffff;
    --charcoal: #454a4a;
    --ink: #4a4a4a;
    --orange: #f6a623;
    --yellow: #ffc214;
    --white: #ffffff;
  }
  * { margin: 0; padding: 0; box-sizing: border-box; }
  html, body {
    width: 1200px; height: 1200px; overflow: hidden;
    background: var(--backdrop);
  }
  .card {
    position: absolute; left: 217px; width: 800px; height: 457px;
  }
  .card--front { top: 115px; background: var(--paper); }
  .card--back { top: 638px; background: var(--charcoal); }

  .brand {
    position: absolute; right: 65px; top: 92px;
    display: flex; align-items: center; gap: 12px;
    font-family: "Roboto", sans-serif; font-weight: 300;
    font-size: 58px; line-height: 1; color: var(--charcoal);
  }
  .brand__dot {
    width: 14px; height: 14px; border-radius: 50%; background: var(--yellow);
  }

  .person { position: absolute; left: 46px; top: 282px; font-family: "Roboto", sans-serif; }
  .person__name { font-size: 30px; font-weight: 400; color: var(--orange); line-height: 1.1; }
  .person__title { font-size: 22px; font-weight: 400; color: var(--ink); letter-spacing: 0.5px; margin-top: 1px; }
  .person__address { font-size: 19px; font-weight: 400; color: #555; margin-top: 10px; }

  .contact-band {
    position: absolute; left: 0; top: 388px; width: 100%; height: 37px;
    background: var(--charcoal); color: var(--white);
    font-family: "Roboto Condensed", sans-serif; font-size: 19px;
    display: flex; align-items: center; padding-left: 46px; gap: 5px;
    white-space: nowrap;
  }
  .contact-band b { font-weight: 700; }

  .back-brand {
    position: absolute; left: 0; right: 0; top: 180px;
    display: flex; justify-content: center; align-items: center; gap: 16px;
    font-family: "Roboto", sans-serif; font-weight: 300;
    font-size: 64px; line-height: 1; color: var(--white);
  }
  .back-brand__dot {
    width: 22px; height: 22px; border-radius: 50%; background: var(--yellow);
  }
  .purpose {
    position: absolute; left: 0; right: 0; top: 380px; text-align: center;
    font-family: "Roboto Condensed", sans-serif; font-style: italic;
    font-size: 22px; color: var(--white);
  }
  .purpose__accent { color: var(--orange); }
</style>
</head>
<body>
  <section class="card card--front">
    <div class="brand"><span class="brand__dot"></span>Larkstone</div>
    <div class="person">
      <p class="person__name">Brennan Ulfsson</p>
      <p class="person__title">CONSULTANT</p>
      <p class="person__address">Level 3, 218 Wexley Street Melbourne 3000</p>
    </div>
    <div class="contact-band">
      <b>P:</b> 0468 927 341 <b>E:</b> brennan@larkstone-partners.com.au <b>W:</b> www.larkstone-partners.com.au
    </div>
  </section>

  <section class="card card--back">
    <div class="back-brand"><span class="back-brand__dot"></span>Larkstone</div>
    <p class="purpose">we build the finest spaces <span class="purpose__accent">where people thrive</span></p>
  </section>
</body>
</html>
```